Website Design for a holiday home letting busines

We require a redesign of our present website www.pinebrookstays.com. We want the website to stand out and look professional and clean to make holiday hunters want to book a caravan or lodge holiday with us. Our logo is red however we DO NOT want the website to be red. We want a natural colour scheme.

The final design should communicate that we are a professional company to book with.

On the home page we require;
Overview of company
Photo
Search box for holiday (check in)
Late Deals
Reviews
News

We would like the following pages designed; home page, available dates page, caravans page, content page.

The website should be responsive for smart phones. One website I do like is http://www.verdoliso.be/nl/

Target Market(s)

Families

Industry/Entity Type

Travel

Number of Pages Required

5+ page

Font styles to use
Serif

Requirements
Must have
• The project must be responsive for mobile phones and tablets.
• Ability to search for holiday home holidays
• We want a natural colour scheme.
Nice to have
• A style we like is http://www.verdoliso.be/nl/
Should not have
• Do not use red as a colour for the website. Our logo is red so this is the only time we want this used.

```html
<!DOCTYPE html>
<html lang="en">
<head>
<meta charset="utf-8">
<title>Pinebrook Stays – Holiday Caravans and Lodges</title>
<link href="https://fonts.googleapis.com/css2?family=Open+Sans:wght@400;600;700&display=swap" rel="stylesheet">
<style>
:root{
  --gold:#c8aa52;
  --gold-dark:#a98c3a;
  --ink:#333333;
  --muted:#777777;
  --paper:#ffffff;
  --soft:#f3f1ec;
  --footer:#2f2f2f;
  --footer-deep:#262626;
  --brand:#b3262b;
  --shade:rgba(0,0,0,.64);
  --photo-a:#a88a62;
  --photo-b:#5e4a35;
}
*{box-sizing:border-box;margin:0;padding:0}
html,body{width:1200px;height:2952px;overflow:hidden}
body{font-family:"Open Sans",Arial,sans-serif;color:var(--ink);background:var(--paper);position:relative}
.page{position:absolute;inset:0}

/* header */
.site-header{height:112px;display:flex;align-items:center;justify-content:space-between;padding:0 100px}
.brand{display:flex;align-items:center;gap:12px;font-weight:700;font-size:26px;color:var(--brand)}
.brand-dot{width:40px;height:40px;border-radius:50%;background:var(--brand)}
.header-tools{display:flex;align-items:center;gap:14px}
.header-search{width:160px;height:30px;border:1px solid #ddd}
.header-btn{width:30px;height:30px;background:var(--gold)}
.main-nav{height:40px;background:#3a3a3a;display:flex;align-items:center;padding:0 100px;gap:34px;font-size:13px;color:#eee}

/* hero */
.hero{position:relative;height:608px;background:linear-gradient(120deg,var(--photo-a),var(--photo-b))}
.hero-caption{position:absolute;right:180px;top:240px;color:#fff;font-size:26px;font-weight:600}
.booking-bar{position:absolute;left:120px;right:120px;bottom:20px;height:52px;display:flex;gap:24px}
.booking-field{flex:1;background:rgba(200,170,82,.9);display:flex;align-items:center;justify-content:space-between;padding:0 18px;color:#fff;font-size:14px}
.booking-field i{width:18px;height:18px;border:2px solid #fff;display:block}
.booking-submit{width:260px;background:#444;color:#fff;display:flex;align-items:center;justify-content:center;font-weight:700;letter-spacing:1px}

/* sections */
.section-title{text-align:center;font-size:24px;font-weight:700;text-transform:uppercase;color:#444}
.welcome{padding:66px 140px 0;height:1020px - 760px}
.welcome p{text-align:center;font-size:13px;line-height:22px;color:var(--muted);margin-top:22px}
.btn-outline{display:block;width:110px;margin:22px auto 0;border:1px solid #bbb;text-align:center;font-size:12px;padding:6px 0;color:var(--muted)}

.cards{display:flex;gap:20px;padding:0 100px;margin-top:32px}
.card{width:320px;height:380px;position:relative;background:linear-gradient(140deg,var(--photo-a),var(--photo-b))}
.card-label{position:absolute;left:0;right:0;bottom:0;height:42px;background:var(--gold);color:#fff;font-size:14px;display:flex;align-items:center;justify-content:center;flex-direction:column;line-height:18px}
.card-icons{position:absolute;right:16px;top:16px;display:flex;gap:8px}
.card-icons span{width:26px;height:26px;background:rgba(255,255,255,.85)}
.card-details{position:absolute;inset:0 0 42px 0;background:rgba(30,30,30,.88);padding:110px 30px 0;color:#ddd;font-size:13px}
.card-details div{display:flex;justify-content:space-between;border-bottom:1px solid #555;padding:8px 0}
.price-tag{position:absolute;right:0;bottom:42px;background:rgba(0,0,0,.55);color:#fff;font-weight:700;font-size:22px;padding:8px 14px}
.dots{display:flex;justify-content:center;gap:8px;margin-top:24px}
.dots span{width:10px;height:10px;border-radius:50%;background:#bbb}
.dots span.on{background:var(--ink)}

.caravans{margin-top:48px}
.deals{margin-top:48px}

.info-band{margin-top:44px;height:460px;background:var(--soft);display:flex;gap:20px;padding:52px 100px 0}
.info-panel{width:320px;height:400px;background:var(--gold);padding:18px 20px;color:#fff}
.info-panel h3{font-size:20px;font-weight:600;margin-bottom:22px}
.item{display:flex;gap:14px;margin-bottom:26px;font-size:12px;line-height:17px}
.thumb{width:60px;height:52px;flex:none;background:linear-gradient(140deg,var(--photo-a),var(--photo-b))}
.thumb.round{border-radius:50%;width:52px}
.blog-photo{height:210px;background:linear-gradient(140deg,#d8cbb5,var(--photo-a))}

/* footer */
.site-footer{position:absolute;left:0;right:0;top:2600px;height:352px;background:var(--footer);color:#ccc;font-size:12px}
.footer-cols{display:flex;justify-content:space-between;padding:24px 100px 0}
.footer-cols h4{color:#fff;font-size:20px;font-weight:600;margin-bottom:12px}
.footer-cols ul{list-style:none;line-height:20px}
.footer-mid{width:320px;padding-top:20px}
.footer-mid .circle{width:70px;height:70px;border-radius:50%;background:#3c3c3c;margin-bottom:16px}
.signup{display:flex;margin-top:14px}
.signup span{flex:1;height:30px;background:#fff}
.signup b{width:34px;height:30px;background:var(--gold)}
.contact li{display:flex;gap:10px;align-items:center}
.contact i{width:10px;height:10px;background:var(--gold);display:block}
.footer-bottom{position:absolute;left:0;right:0;bottom:0;height:52px;background:var(--footer-deep);display:flex;align-items:center;justify-content:space-between;padding:0 100px}
.socials,.payments{display:flex;gap:10px}
.socials span{width:22px;height:22px;border-radius:50%;background:#555}
.payments span{width:38px;height:24px;background:#555}

/* login overlay */
.shade{position:absolute;inset:0;background:var(--shade)}
.login{position:absolute;left:368px;top:220px;width:360px;height:312px;background:#fff;padding:18px 20px}
.login h2{font-size:22px;font-weight:700;margin-bottom:18px}
.close{position:absolute;right:-10px;top:-10px;width:24px;height:24px;border-radius:50%;background:#fff;border:2px solid #333;font-size:13px;text-align:center;line-height:19px;font-weight:700}
.field{height:36px;border:1px solid #ccc;display:flex;align-items:center;gap:10px;padding:0 12px;color:#999;font-size:13px;margin-bottom:12px}
.field svg{flex:none}
.login-actions{display:flex;gap:10px;margin-top:6px}
.login-actions span{width:80px;height:34px;display:flex;align-items:center;justify-content:center;color:#fff;font-size:13px;font-weight:700}
.btn-login{background:var(--gold)}
.btn-signin{background:#333}
.login-foot{display:flex;gap:22px;font-size:12px;color:#666;margin-top:24px;align-items:center}
.login-foot i{width:12px;height:12px;border:1px solid #999;display:inline-block;vertical-align:middle;margin-right:6px}
</style>
</head>
<body>
<div class="page">
  <header class="site-header">
    <div class="brand"><span class="brand-dot"></span>Pinebrook Stays</div>
    <div class="header-tools"><span class="header-search"></span><span class="header-btn"></span></div>
  </header>
  <nav class="main-nav">
    <span>Home</span><span>Blog</span><span>Reviews</span><span>Available Dates</span><span>Our Caravans</span><span>Our Lodges</span><span>Late Deals</span><span>Things to Do</span><span>Contact Us</span>
  </nav>

  <section class="hero" role="img" aria-label="Photo of a bright caravan lounge with sofa and windows">
    <div class="hero-caption">Relax in Your Holiday Home</div>
    <div class="booking-bar">
      <div class="booking-field">Check in date <i></i></div>
      <div class="booking-field">Number of nights <i></i></div>
      <div class="booking-submit">SEARCH</div>
    </div>
  </section>

  <section class="welcome" style="height:auto">
    <h2 class="section-title" style="margin-top:0">Welcome to Pinebrook Stays</h2>
    <p>We are a family run business offering quality holiday caravans and lodges in peaceful countryside parks across the region. Every home is cleaned, checked and fully equipped so your stay is simple from the moment you arrive. Choose from cosy caravans for small groups or spacious lodges for the whole family, with short breaks and week long stays available all year round.</p>
    <span class="btn-outline">Read more</span>
  </section>

  <section class="caravans">
    <h2 class="section-title">Our Caravans and Lodges</h2>
    <div class="cards">
      <div class="card" role="img" aria-label="Photo of a caravan interior">
        <div class="card-icons"><span></span><span></span></div>
        <div class="card-details">
          <div><span>Caravan type</span><span>Lodge</span></div>
          <div><span>Berths</span><span>Six berth</span></div>
          <div><span>Sleeps</span><span>6</span></div>
          <div><span>Bedrooms</span><span>3</span></div>
        </div>
        <div class="card-label">Willow Lodge</div>
      </div>
      <div class="card" role="img" aria-label="Photo of a caravan living room">
        <div class="card-icons"><span></span><span></span></div>
        <div class="card-label">Oak Caravan</div>
      </div>
      <div class="card" role="img" aria-label="Photo of a lodge kitchen and lounge">
        <div class="card-icons"><span></span><span></span></div>
        <div class="card-label">Birch Lodge</div>
      </div>
    </div>
    <div class="dots"><span class="on"></span><span></span></div>
  </section>

  <section class="deals">
    <h2 class="section-title">Late Deals</h2>
    <div class="cards">
      <div class="card" role="img" aria-label="Photo of a caravan interior on offer">
        <div class="card-icons"><span></span><span></span></div>
        <div class="price-tag">£199</div>
        <div class="card-label">Hazel Caravan<br><small>Arrive 12 June · 7 nights</small></div>
      </div>
      <div class="card" role="img" aria-label="Photo of a lodge interior on offer">
        <div class="card-icons"><span></span><span></span></div>
        <div class="price-tag">£249</div>
        <div class="card-label">Maple Lodge<br><small>Arrive 14 June · 4 nights</small></div>
      </div>
      <div class="card" role="img" aria-label="Photo of a caravan lounge on offer">
        <div class="card-icons"><span></span><span></span></div>
        <div class="price-tag">£179</div>
        <div class="card-label">Elm Caravan<br><small>Arrive 19 June · 3 nights</small></div>
      </div>
    </div>
    <div class="dots"><span class="on"></span><span></span></div>
  </section>

  <section class="info-band">
    <div class="info-panel">
      <h3>Recent News</h3>
      <div class="item"><span class="thumb" role="img" aria-label="News photo"></span><span>New lodges open this summer on the lakeside park.<br>12 May</span></div>
      <div class="item"><span class="thumb" role="img" aria-label="News photo"></span><span>Family fun week returns with walks and games.<br>4 May</span></div>
      <div class="item"><span class="thumb" role="img" aria-label="News photo"></span><span>Pet friendly caravans now available to book.<br>28 April</span></div>
    </div>
    <div class="info-panel">
      <h3>Customer Reviews</h3>
      <div class="item"><span class="thumb round" role="img" aria-label="Guest avatar"></span><span>Spotless caravan and a lovely quiet park, we will be back.<br>Sarah</span></div>
      <div class="item"><span class="thumb round" role="img" aria-label="Guest avatar"></span><span>The kids loved the lodge, booking was quick and easy.<br>Mark</span></div>
      <div class="item"><span class="thumb round" role="img" aria-label="Guest avatar"></span><span>Great value break with friendly helpful owners.<br>Helen</span></div>
    </div>
    <div class="info-panel">
      <h3>Blog</h3>
      <div class="blog-photo" role="img" aria-label="Photo of a caravan bedroom"></div>
      <div class="item" style="margin-top:16px"><span>Ten things to pack for a family caravan holiday.<br>Read more</span></div>
    </div>
  </section>

  <footer class="site-footer">
    <div class="footer-cols">
      <div>
        <h4>QUICK LINK</h4>
        <ul><li>Home</li><li>Blog</li><li>Reviews</li><li>Available Dates</li><li>Our Caravans</li><li>Our Lodges</li><li>Late Deals</li><li>Contact Us</li></ul>
      </div>
      <div class="footer-mid">
        <div class="circle"></div>
        <p>Sign up to our newsletter for late deals and news from our parks.</p>
        <div class="signup"><span></span><b></b></div>
      </div>
      <div>
        <h4>CONTACT US</h4>
        <ul class="contact">
          <li><i></i>01632 960 418</li>
          <li><i></i>hello@pinebrookstays.com</li>
          <li><i></i>www.pinebrookstays.com</li>
          <li><i></i>14 Meadow Lane, Pinebrook</li>
          <li><i></i>Open daily 9am to 6pm</li>
        </ul>
      </div>
    </div>
    <div class="footer-bottom">
      <span>© Pinebrook Stays. All rights reserved.</span>
      <div class="socials"><span></span><span></span><span></span></div>
      <div class="payments"><span></span><span></span></div>
    </div>
  </footer>
</div>

<div class="shade"></div>
<div class="login">
  <span class="close">×</span>
  <h2>Member Log In</h2>
  <div class="field">
    <svg width="14" height="14" viewBox="0 0 14 14"><circle cx="7" cy="4" r="3" fill="#555"/><path d="M1 14c0-4 3-6 6-6s6 2 6 6z" fill="#555"/></svg>User name
  </div>
  <div class="field">
    <svg width="14" height="14" viewBox="0 0 14 14"><rect x="2" y="6" width="10" height="8" fill="#555"/><path d="M4 6V4a3 3 0 0 1 6 0v2" stroke="#555" stroke-width="1.6" fill="none"/></svg>Password
  </div>
  <div class="login-actions"><span class="btn-login">LOG IN</span><span class="btn-signin">SIGN IN</span></div>
  <div class="login-foot"><span><i></i>Remember me</span><span>Forgot your Password?</span></div>
</div>
</body>
</html>
```